WP website design (Valkmor)

We need a wordpress design for an established auction and real estate company based in Kansas. The winning design will incorporate a professional color scheme with company logo in a clean layout. The design needs to consider that this will be developed on a responsive theme. Colors are blue and gray, with perhaps an accent/highlight color.

Industry/Entity Type

Real Estate

Font styles to use
Serif
Sans Serif

Colors

Designer to choose colors to be used in the design.

Requirements
Must have
• Navigation:
1) Home 2) Auctions 3) Real Estate Listings 4) Buyers 5) Sellers 6) About Us 7) Contact Us 7) Brokers

Page will have slideshow, please use any stock real estate image initially. Homepage will have auctions - as at http://brindlegavelhouse.com/upcoming-auctions/. Footer will have smaller company logo and attached association logos.

Widgets:
1) email sign up 2) Social media (twitter, FB, youtube, RSS) 3) News & Events blog 4) Video Player
Nice to have
• demonstrate the drop-down menu styling, Past Auctions - under the main Auctions tab

```html
<!DOCTYPE html>
<html lang="en">
<head>
<meta charset="utf-8">
<title>Valkmor Auction/Realty, LLC</title>
<link href="https://fonts.googleapis.com/css2?family=Libre+Baskerville:wght@400;700&family=Open+Sans:wght@400;600;700&display=swap" rel="stylesheet">
<style>
:root{
  --navy:#1b4677;
  --blue:#2a5b92;
  --blue-light:#3c72ad;
  --ink:#333a42;
  --muted:#7a828b;
  --gray-bg:#737a82;
  --card:#ffffff;
  --line:#d7dbe0;
  --btn-gray:#8d959d;
  --footer:#e5e7ea;
  --footer-bar:#d2d6da;
  --hero-a:#8fb3d6;
  --hero-b:#6f8a5a;
  --caption:rgba(24,48,78,.82);
}
*{margin:0;padding:0;box-sizing:border-box}
html,body{width:1200px;height:2196px;overflow:hidden}
body{font-family:"Open Sans",Arial,sans-serif;color:var(--ink);background:var(--gray-bg);position:relative}

/* brand lockup */
.brand{display:flex;align-items:center;gap:12px}
.brand-mark{flex:none;width:34px;height:34px;border-radius:50%;background:var(--navy)}
.brand-name{font-family:"Libre Baskerville",Georgia,serif;font-weight:700;font-size:24px;color:var(--navy);line-height:1;white-space:nowrap}
.brand-sub{font-family:"Libre Baskerville",Georgia,serif;font-size:15px;color:var(--navy);line-height:1.3;margin-left:14px;white-space:nowrap}

/* header */
.site-header{position:absolute;left:0;top:0;width:1200px;height:112px;background:#fff}
.site-header .brand{position:absolute;left:140px;top:26px}
.search{position:absolute;left:780px;top:30px;width:300px;height:30px;display:flex}
.search input{flex:1;border:1px solid #b9c0c8;font:12px "Open Sans",sans-serif;padding:0 10px;color:var(--muted)}
.search button{width:32px;border:0;background:var(--navy);display:flex;align-items:center;justify-content:center}

.main-nav{position:absolute;left:0;top:112px;width:1200px;height:28px;background:var(--navy)}
.main-nav ul{list-style:none;display:flex;position:absolute;left:120px;top:0;height:28px}
.main-nav li{position:relative;color:#fff;font-size:12px;font-weight:700;letter-spacing:.5px;line-height:28px;padding:0 22px}
.main-nav li.active{background:var(--blue-light)}
.dropdown{position:absolute;left:0;top:28px;width:112px;background:var(--navy);z-index:5;border-top:2px solid var(--blue-light)}
.dropdown span{display:block;font-size:11px;font-weight:400;line-height:20px;padding:0 12px;border-bottom:1px solid rgba(255,255,255,.15)}

/* hero */
.hero{position:absolute;left:0;top:140px;width:1200px;height:402px;background:linear-gradient(180deg,var(--hero-a) 0%,#c9d6e0 45%,var(--hero-b) 100%)}
.hero-arrow{position:absolute;top:170px;width:30px;height:40px;background:rgba(0,0,0,.35);display:flex;align-items:center;justify-content:center}
.hero-caption{position:absolute;left:0;bottom:0;width:1200px;height:100px;background:var(--caption);padding:18px 0 0 120px;color:#fff}
.hero-caption h1{font-family:"Libre Baskerville",Georgia,serif;font-weight:400;font-size:32px;line-height:1.2}
.hero-caption p{font-family:"Libre Baskerville",Georgia,serif;font-size:16px;margin-top:4px;color:#dfe7f0}

/* listing cards */
.listing{position:absolute;left:124px;width:656px;height:212px;background:var(--card);box-shadow:0 2px 4px rgba(0,0,0,.25);padding:18px 24px}
.listing h2{font-family:"Libre Baskerville",Georgia,serif;font-weight:400;font-size:26px;color:var(--blue)}
.listing hr{border:0;border-top:1px solid var(--line);margin:12px 0 16px}
.listing .thumb{position:absolute;left:24px;top:88px;width:116px;height:80px;background:linear-gradient(180deg,#9fbad2,#b9b09a 60%,#6f8659)}
.listing .dates{position:absolute;left:160px;top:92px;font-size:13px;line-height:20px;color:var(--ink)}
.listing .posted{position:absolute;left:26px;top:180px;font-size:10px;color:var(--muted);display:flex;align-items:center;gap:5px}
.btn{position:absolute;top:150px;height:26px;line-height:26px;font-size:12px;color:#fff;text-align:center;border-radius:2px}
.btn-gray{left:410px;width:76px;background:var(--btn-gray)}
.btn-blue{left:494px;width:88px;background:var(--blue)}

.showing{position:absolute;left:124px;top:1782px;width:656px;text-align:center;font-size:11px;font-weight:700;color:#eef1f4;letter-spacing:.5px}
.load-more{position:absolute;left:340px;top:1820px;width:224px;height:48px;background:var(--navy);color:#fff;font-size:15px;font-weight:600;text-align:center;line-height:48px;box-shadow:0 2px 4px rgba(0,0,0,.3)}

/* sidebar */
.widget{position:absolute;left:800px;width:280px;background:var(--card);box-shadow:0 2px 4px rgba(0,0,0,.25)}
.subscribe{top:580px;height:346px;padding:22px 20px}
.widget h3{font-family:"Libre Baskerville",Georgia,serif;font-weight:400;font-size:24px;color:var(--blue);line-height:1.2}
.subscribe .head{display:flex;gap:12px;align-items:center}
.subscribe p{font-size:12px;line-height:18px;color:var(--muted);margin-top:16px}
.subscribe .email{margin-top:22px;height:36px;border:1px solid #c5cbd2;font-size:12px;color:var(--muted);line-height:34px;padding:0 10px}
.subscribe .signup{margin-top:16px;height:42px;background:var(--navy);color:#fff;font-size:15px;font-weight:700;text-align:center;line-height:42px;letter-spacing:.5px}

.upcoming{top:952px;height:410px}
.upcoming .photo{height:160px;background:linear-gradient(180deg,#c8d5e2,#9aa9b8 60%,#6d7c8d)}
.upcoming .body{padding:18px 20px}
.upcoming .meta{font-size:10px;color:var(--muted);margin-top:4px}
.upcoming p{font-size:11px;line-height:17px;color:var(--muted);margin-top:14px}
.upcoming .more{font-size:11px;font-weight:700;color:var(--navy);margin-top:12px}

.video{top:1362px;height:132px;background:linear-gradient(180deg,#58656f,#3a3f45)}
.video .controls{position:absolute;left:0;bottom:0;width:100%;height:24px;background:#1e2226;display:flex;align-items:center;gap:10px;padding:0 10px}
.video .bar{flex:1;height:4px;background:#555}
.video .bar i{display:block;width:35%;height:4px;background:var(--blue-light)}

.share{top:1520px;height:240px;padding:22px 20px}
.share p{font-size:13px;line-height:19px;color:var(--muted);margin-top:12px}
.share .icons{display:flex;gap:12px;margin-top:26px}
.share .icons span{width:48px;height:48px;border-radius:3px;background:var(--blue)}
.share .icons span:nth-child(2){background:var(--navy)}
.share .icons span:nth-child(3){background:#b5443a}

/* footer */
.site-footer{position:absolute;left:0;top:1908px;width:1200px;height:288px;background:var(--footer)}
.footer-brand{position:absolute;left:140px;top:40px;width:220px}
.footer-brand .brand-mark{width:24px;height:24px}
.footer-brand .brand-name{font-size:19px}
.footer-brand .brand-sub{margin:8px 0 0;font-size:12px}
.footer-social{position:absolute;left:140px;top:166px;display:flex;gap:10px}
.footer-social span{width:30px;height:30px;border-radius:50%;background:var(--navy)}
.badges{position:absolute;left:380px;top:48px;width:380px;display:flex;flex-wrap:wrap;gap:14px 18px}
.badges span{display:block;background:#2c3138}
.footer-col{position:absolute;top:44px;font-size:12px;color:var(--ink)}
.footer-col h4{font-size:13px;font-weight:700;color:var(--navy);letter-spacing:.5px;margin-bottom:8px}
.footer-col li{list-style:none;line-height:22px;color:var(--muted);padding-left:12px;position:relative}
.footer-col li::before{content:"";position:absolute;left:0;top:9px;width:4px;height:4px;background:var(--blue);border-radius:50%}
.footer-bar{position:absolute;left:0;bottom:0;width:1200px;height:34px;background:var(--footer-bar);font-size:11px;color:var(--muted);line-height:34px}
.footer-bar .copy{position:absolute;left:140px}
.footer-bar .links{position:absolute;right:120px}
</style>
</head>
<body>

<header class="site-header">
  <div class="brand">
    <span class="brand-mark"></span>
    <span class="brand-name">Heartland Ridge</span>
    <span class="brand-sub">Valkmor<br>Auction/Realty, LLC</span>
  </div>
  <form class="search">
    <input type="text" value="Search Real Estate, Brokers, etc.">
    <button type="button" aria-label="Search"><svg width="14" height="14" viewBox="0 0 14 14"><circle cx="6" cy="6" r="4.5" fill="none" stroke="#fff" stroke-width="2"/><line x1="9.5" y1="9.5" x2="13" y2="13" stroke="#fff" stroke-width="2"/></svg></button>
  </form>
</header>

<nav class="main-nav">
  <ul>
    <li>HOME</li>
    <li class="active">AUCTIONS
      <div class="dropdown"><span>Past Auctions</span><span>Upcoming</span></div>
    </li>
    <li>REAL ESTATE LISTINGS</li>
    <li>BUYERS</li>
    <li>SELLERS</li>
    <li>BROKERS</li>
    <li>ABOUT</li>
    <li>CONTACT</li>
  </ul>
</nav>

<section class="hero" role="img" aria-label="Slideshow photo of a two-storey suburban house with a green lawn under a blue sky">
  <div class="hero-arrow" style="left:0"><svg width="12" height="18"><polyline points="10,2 3,9 10,16" fill="none" stroke="#fff" stroke-width="3"/></svg></div>
  <div class="hero-arrow" style="right:0"><svg width="12" height="18"><polyline points="2,2 9,9 2,16" fill="none" stroke="#fff" stroke-width="3"/></svg></div>
  <div class="hero-caption">
    <h1>Trusted Online Real Estate Marketplace</h1>
    <p>home auctions, trustee sale foreclosure auctions, commercial real estate</p>
  </div>
</section>

<main>
  <article class="listing" style="top:580px">
    <h2>Single Family Residence | Dallas,TX</h2><hr>
    <div class="thumb" role="img" aria-label="Photo of the listed house"></div>
    <div class="dates">Begins: Tuesday, March 04, 2014 at 10:00 AM EST<br>Ends: Tuesday, March 11, 2014 at 11:00 PM EST</div>
    <div class="btn btn-gray">Videos</div><div class="btn btn-blue">View Details</div>
    <div class="posted"><svg width="9" height="9"><circle cx="4.5" cy="4.5" r="3.5" fill="none" stroke="#7a828b"/></svg>Posted: 03/11/2014</div>
  </article>
  <article class="listing" style="top:822px">
    <h2>Single Family Residence | Dallas,TX</h2><hr>
    <div class="thumb" role="img" aria-label="Photo of the listed house"></div>
    <div class="dates">Begins: Tuesday, March 04, 2014 at 10:00 AM EST<br>Ends: Tuesday, March 11, 2014 at 11:00 PM EST</div>
    <div class="btn btn-gray">Videos</div><div class="btn btn-blue">View Details</div>
    <div class="posted"><svg width="9" height="9"><circle cx="4.5" cy="4.5" r="3.5" fill="none" stroke="#7a828b"/></svg>Posted: 03/11/2014</div>
  </article>
  <article class="listing" style="top:1064px">
    <h2>Single Family Residence | Dallas,TX</h2><hr>
    <div class="thumb" role="img" aria-label="Photo of the listed house"></div>
    <div class="dates">Begins: Tuesday, March 04, 2014 at 10:00 AM EST<br>Ends: Tuesday, March 11, 2014 at 11:00 PM EST</div>
    <div class="btn btn-gray">Videos</div><div class="btn btn-blue">View Details</div>
    <div class="posted"><svg width="9" height="9"><circle cx="4.5" cy="4.5" r="3.5" fill="none" stroke="#7a828b"/></svg>Posted: 03/11/2014</div>
  </article>
  <article class="listing" style="top:1306px">
    <h2>Single Family Residence | Dallas,TX</h2><hr>
    <div class="thumb" role="img" aria-label="Photo of the listed house"></div>
    <div class="dates">Begins: Tuesday, March 04, 2014 at 10:00 AM EST<br>Ends: Tuesday, March 11, 2014 at 11:00 PM EST</div>
    <div class="btn btn-gray">Videos</div><div class="btn btn-blue">View Details</div>
    <div class="posted"><svg width="9" height="9"><circle cx="4.5" cy="4.5" r="3.5" fill="none" stroke="#7a828b"/></svg>Posted: 03/11/2014</div>
  </article>
  <article class="listing" style="top:1548px">
    <h2>Single Family Residence | Dallas,TX</h2><hr>
    <div class="thumb" role="img" aria-label="Photo of the listed house"></div>
    <div class="dates">Begins: Tuesday, March 04, 2014 at 10:00 AM EST<br>Ends: Tuesday, March 11, 2014 at 11:00 PM EST</div>
    <div class="btn btn-gray">Videos</div><div class="btn btn-blue">View Details</div>
    <div class="posted"><svg width="9" height="9"><circle cx="4.5" cy="4.5" r="3.5" fill="none" stroke="#7a828b"/></svg>Posted: 03/11/2014</div>
  </article>

  <div class="showing">SHOWING 1-5 OF 6,290</div>
  <div class="load-more">Load More Listings</div>

  <aside>
    <section class="widget subscribe">
      <div class="head">
        <svg width="28" height="20" viewBox="0 0 28 20"><rect x="1" y="1" width="26" height="18" fill="none" stroke="#7a828b" stroke-width="2"/><polyline points="1,1 14,11 27,1" fill="none" stroke="#7a828b" stroke-width="2"/></svg>
        <h3>Subscribe to us</h3>
      </div>
      <p>Stay updated with all our latest news and auctions, just enter your email address below and we will keep you posted.</p>
      <div class="email">Your email address...</div>
      <div class="signup">SIGN UP TODAY</div>
    </section>

    <section class="widget upcoming">
      <div class="photo" role="img" aria-label="News photo of an auction event"></div>
      <div class="body">
        <h3>Upcoming Auctions</h3>
        <div class="meta">Date Posted 03/18/2014</div>
        <p>Residential and farm land properties go on the block this month. Register early to preview each lot, review the terms and bid online or in person at our Kansas office.</p>
        <div class="more">READ MORE</div>
      </div>
    </section>

    <section class="widget video" role="img" aria-label="Video player showing a property tour">
      <div class="controls">
        <svg width="10" height="12"><polygon points="0,0 10,6 0,12" fill="#fff"/></svg>
        <div class="bar"><i></i></div>
        <svg width="14" height="12"><rect x="0" y="3" width="5" height="6" fill="#fff"/><polygon points="5,3 11,0 11,12 5,9" fill="#fff"/></svg>
      </div>
    </section>

    <section class="widget share">
      <h3>Share to friends!</h3>
      <p>Join the auction on our social pages. Get exclusive deals &amp; updates!</p>
      <div class="icons"><span></span><span></span><span></span></div>
    </section>
  </aside>
</main>

<footer class="site-footer">
  <div class="footer-brand">
    <div class="brand"><span class="brand-mark"></span><span class="brand-name">Heartland Ridge</span></div>
    <div class="brand-sub">Valkmor Auction/Realty, LLC</div>
  </div>
  <div class="footer-social"><span></span><span></span><span></span><span></span></div>

  <div class="badges" aria-label="Association memberships">
    <span style="width:54px;height:44px"></span>
    <span style="width:70px;height:44px;background:#7a2a2a"></span>
    <span style="width:54px;height:44px"></span>
    <span style="width:50px;height:44px;background:#4b4f55"></span>
    <span style="width:70px;height:44px;background:#fff;border:3px solid #2c3138"></span>
    <span style="width:90px;height:40px;background:#3f6b3a"></span>
    <span style="width:40px;height:40px"></span>
    <span style="width:40px;height:40px;background:#4b4f55"></span>
  </div>

  <div class="footer-col" style="left:820px">
    <h4>ABOUT</h4>
    <ul><li>history</li><li>team</li><li>blog</li></ul>
  </div>
  <div class="footer-col" style="left:960px">
    <h4>CONTACT</h4>
    <ul><li>office map</li><li>help</li><li>careers</li><li>sitemap</li></ul>
  </div>

  <div class="footer-bar">
    <span class="copy">© 2014 Heartland Ridge. All Rights Reserved</span>
    <span class="links">Site Map | Privacy Policy | Terms of Use</span>
  </div>
</footer>

</body>
</html>
```